I need a business card to launch my business. I am a carpenter who works with wood and metal framing. I do commercial and residential properties. I do the final fixtures in expensive residential properties. For example custom made wardrobes, prefinished doors and skirtings. I have an eye for detail and take pride in my work.

I don't want to be pigeon holed as a guy with a tool belt and a hammer. I want to look like a professional company. I want my logo to be modern and young and edgy. I don't have any preference for colours but don't want yellow.

Industry/Entity Type

Residential

Contact Information for Business Card

Oakridge Joinery Co
specialising in residential and commercial fit outs

Mark Delaney
Phone: 0417 358 260
oakridgejoineryco@mailbox-example.net

Logo styles of interest
Pictorial/Combination Logo
Wordmark Logo
Lettermark Logo

```html
<!DOCTYPE html>
<html lang="en">
<head>
<meta charset="UTF-8">
<title>Oakridge Joinery Co — Business Card</title>
<link href="https://fonts.googleapis.com/css2?family=Cabin:wght@400;500&display=swap" rel="stylesheet">
<style>
  :root {
    --page-top: #ffffff;
    --page-stage: #000000;
    --card-bg: #ffffff;
    --card-edge: #9a9a9a;
    --grain-soft: #eeeeee;
    --brand-brown: #7a4f1e;
    --rule-brown: #8a4a1c;
    --ink: #1a1a1a;
    --wood-light: #b08550;
    --wood-dark: #8c6230;
  }
  * { margin: 0; padding: 0; box-sizing: border-box; }
  html, body {
    width: 1200px;
    height: 1185px;
    overflow: hidden;
  }
  body {
    position: relative;
    background: var(--page-stage);
    font-family: "Cabin", sans-serif;
  }
  .top-band {
    position: absolute;
    left: 0; top: 0;
    width: 1200px; height: 185px;
    background: var(--page-top);
  }
  .business-card {
    position: absolute;
    left: 217px; top: 463px;
    width: 766px; height: 443px;
    border: 1px solid var(--card-edge);
    background:
      radial-gradient(ellipse 260px 50px at 600px 230px, var(--grain-soft), transparent 70%),
      radial-gradient(ellipse 420px 90px at 520px 240px, #f5f5f5, transparent 75%),
      var(--card-bg);
    overflow: hidden;
  }
  .timber-panel {
    position: absolute;
    left: 214px; top: 0;
    width: 309px; height: 109px;
    background: linear-gradient(100deg, var(--wood-dark), var(--wood-light) 45%, var(--wood-dark));
  }
  .brand-name {
    position: absolute;
    left: 0; right: 0;
    top: 182px;
    text-align: center;
    font-size: 40px;
    font-weight: 500;
    letter-spacing: 1px;
    color: var(--brand-brown);
  }
  .contact-row {
    position: absolute;
    left: 53px;
    top: 340px;
    width: 656px;
    height: 46px;
    border-top: 1px solid var(--rule-brown);
    border-bottom: 1px solid var(--rule-brown);
    display: flex;
    align-items: center;
    justify-content: space-between;
  }
  .contact-name {
    font-size: 25px;
    color: var(--brand-brown);
  }
  .contact-item {
    display: flex;
    align-items: center;
    gap: 8px;
    font-size: 16px;
    color: var(--ink);
  }
  .contact-badge {
    display: inline-flex;
    align-items: center;
    justify-content: center;
    width: 17px; height: 17px;
    background: var(--brand-brown);
    color: #fff;
    font-size: 12px;
    font-weight: 500;
  }
</style>
</head>
<body>
  <div class="top-band"></div>

  <div class="business-card">
    <div class="timber-panel" role="img" aria-label="Row of vertical timber planks with natural wood grain"></div>

    <div class="brand-name">Oakridge Joinery Co</div>

    <div class="contact-row">
      <span class="contact-name">Mark Delaney</span>
      <span class="contact-item"><span class="contact-badge">P</span>0417 358 260</span>
      <span class="contact-item"><span class="contact-badge">E</span>oakridgejoineryco@mailbox-example.net</span>
    </div>
  </div>
</body>
</html>
```